Marwick Law Letterhead

We need a new letterhead design for a Law Firm. The address for the law firm is 1475 Calloway Street, Suite 210, Houston, Texas 77041. Phone Number: 832-361-9027; Fax Number: 832-614-7359. The logo is uploaded to the project.

```html
<!DOCTYPE html>
<html lang="en">
<head>
<meta charset="utf-8">
<title>Marwick Law Letterhead</title>
<link href="https://fonts.googleapis.com/css2?family=Roboto:wght@400&family=Cormorant+Garamond:wght@600&display=swap" rel="stylesheet">
<style>
  :root {
    --backdrop: #e2e2e2;
    --paper: #f0f0f0;
    --navy: #16264f;
    --red: #a51c24;
    --ink: #2b2b2b;
    --violet: #7a3a5e;
    --blue: #44508f;
  }
  html, body {
    margin: 0;
    width: 1069px;
    height: 1200px;
    overflow: hidden;
    background: var(--backdrop);
  }
  .letterhead {
    position: absolute;
    left: 119px;
    top: 13px;
    width: 830px;
    height: 1173px;
    background: var(--paper);
    box-shadow: 0 6px 24px rgba(0,0,0,0.12);
    font-family: "Roboto", Arial, sans-serif;
    color: var(--ink);
  }
  .brand {
    position: absolute;
    left: 48px;
    top: 78px;
    display: flex;
    align-items: center;
    gap: 14px;
  }
  .brand-mark {
    width: 44px;
    height: 44px;
    background: var(--navy);
  }
  .brand-name {
    font-family: "Cormorant Garamond", Georgia, serif;
    font-weight: 600;
    font-size: 46px;
    line-height: 1;
    color: var(--navy);
    white-space: nowrap;
  }
  .address {
    position: absolute;
    right: 201px;
    top: 62px;
    text-align: right;
    font-size: 16.5px;
    line-height: 21px;
    color: #1d1d1d;
  }
  .divider {
    position: absolute;
    left: 641px;
    top: 71px;
    width: 1.5px;
    height: 48px;
    background: var(--red);
  }
  .contact {
    position: absolute;
    left: 656px;
    top: 69px;
    font-size: 16.5px;
    line-height: 27px;
    color: #1d1d1d;
  }
  .contact-row {
    display: flex;
    align-items: center;
    gap: 6px;
  }
  .contact-row svg { width: 13px; height: 13px; }
  .header-rule {
    position: absolute;
    top: 146px;
    left: 451px;
    right: 0;
    height: 1.5px;
    background: linear-gradient(to right, var(--red) 0 206px, var(--navy) 206px 100%);
  }
  .recipient {
    position: absolute;
    left: 48px;
    top: 331px;
    font-size: 15.4px;
    line-height: 24px;
  }
  .body-copy {
    position: absolute;
    left: 48px;
    width: 735px;
    font-size: 15.4px;
    line-height: 24px;
    text-align: justify;
    hyphens: auto;
    -webkit-hyphens: auto;
    margin: 0;
  }
  .p1 { top: 443px; }
  .p2 { top: 588px; }
  .p3 { top: 728px; }
  .closing {
    position: absolute;
    left: 48px;
    top: 839px;
    font-size: 15.4px;
    line-height: 24px;
  }
  .signature {
    position: absolute;
    left: 48px;
    top: 879px;
    width: 150px;
    height: 60px;
    background: linear-gradient(to right, #dcdcdc, #e8e8e8);
  }
  .footer-band {
    position: absolute;
    left: 0;
    bottom: 0;
    width: 100%;
    height: 13.5px;
    display: flex;
  }
  .footer-band .navy { width: 276px; background: var(--navy); }
  .footer-band .red { width: 278px; background: var(--red); }
  .footer-band .fade { flex: 1; background: linear-gradient(to right, var(--violet), var(--blue)); }
</style>
</head>
<body>
  <div class="letterhead">
    <div class="brand">
      <div class="brand-mark"></div>
      <div class="brand-name">Marwick Law</div>
    </div>

    <div class="address">
      1475 Calloway Street<br>
      Suite 210, Houston<br>
      Texas 77041
    </div>
    <div class="divider"></div>
    <div class="contact">
      <div class="contact-row">
        <svg viewBox="0 0 16 16" aria-hidden="true"><path fill="#a51c24" d="M1 6c0-2 3-4 7-4s7 2 7 4v1h-3V5.5c-1-.5-2.5-.8-4-.8s-3 .3-4 .8V7H1z M4 8h8l2 6H2z"/><circle cx="8" cy="11" r="1.6" fill="#f0f0f0"/></svg>
        <span>832-361-9027</span>
      </div>
      <div class="contact-row">
        <svg viewBox="0 0 16 16" aria-hidden="true"><path fill="#a51c24" d="M4 1h8v4H4z M1 6h14v6h-3v3H4v-3H1z"/><rect x="5" y="10" width="6" height="4" fill="#f0f0f0"/></svg>
        <span>832-614-7359</span>
      </div>
    </div>
    <div class="header-rule"></div>

    <div class="recipient">
      Mr/s<br>
      First Name and Last Name<br>
      Company Name<br>
      Address
    </div>

    <p class="body-copy p1">Lorem Ipsum is simply dummy text of the printing and typesetting industry. Lorem Ipsum has been the industry's standard dummy text ever since the 1500s, when an unknown printer took a galley of type and scrambled it to make a type specimen book. It has survived not only five centuries, but also the leap into electronic typesetting, remaining essentially unchanged. It was popularised in the 1960s with the release of Lettrawell sheets containing Lorem Ipsum passages.</p>

    <p class="body-copy p2">he standard chunk of Lorem Ipsum used since the 1500s is reproduced below for those interested. Sections 1.10.32 and 1.10.33 from "de Finibus Bonorum et Malorum" by Corvin are also reproduced in their exact original form, accompanied by English versions from the 1914 translation by J. Penwick. Lorem ipsum dolor sit amet, consectetur adipiscing elit, sed do eiusmod tempor incididunt ut labore et dolore magna aliqua.</p>

    <p class="body-copy p3">It is a long established fact that a reader will be distracted by the readable content of a page when looking at its layout. The point of using Lorem Ipsum is that it has a more-or-less normal distribution of letters, as opposed to using 'Content here, content here', making it look like readable English. Many desktop publishing packages and web page editors now .</p>

    <div class="closing">Your Sincerely,</div>
    <div class="signature" role="img" aria-label="Handwritten signature"></div>

    <div class="footer-band">
      <div class="navy"></div>
      <div class="red"></div>
      <div class="fade"></div>
    </div>
  </div>
</body>
</html>
```